full stationary design for a modern sleek design company

we are a design company that does modern minimalistic interior design works as well as other design services for high end clients.
we need a full stationary design including and not limited to (double sided business card, letter head, envelopes, documents folder...etc) that reflects the modern style design we do.
sleek modern and minimalistic is the requirements.
Updates

please use the latest attached files as there was a slight modification on the logo Added Wednesday, March 1, 2017

minor update on the logo files in JPG and PSD has been updated kindly follow the new attachments. Added Thursday, March 2, 2017

Target Market(s)

modern minimalist clients

Industry/Entity Type

Design Agency

Requirements
Must have
• the logo
Nice to have
• i like the colors in the colored 3D logo attached
Should not have
• too many colors

```html
<!DOCTYPE html>
<html lang="en">
<head>
<meta charset="utf-8">
<title>Linea Atelier — Stationery Set</title>
<link rel="stylesheet" href="https://fonts.googleapis.com/css2?family=Montserrat:wght@400;500;600;700&display=swap">
<style>
  :root {
    --orange: #e8912a;
    --charcoal: #3d3d3d;
    --ink: #4a4a4a;
    --muted: #8a8a8a;
    --paper: #fbfbfb;
    --ground: #f2f2f2;
    --rule: #474747;
  }
  * { box-sizing: border-box; margin: 0; padding: 0; }
  html, body { width: 1200px; height: 903px; overflow: hidden; }
  body {
    position: relative;
    background: var(--ground);
    font-family: "Montserrat", sans-serif;
    color: var(--ink);
  }
  .sheet { position: absolute; background: var(--paper); box-shadow: 0 2px 6px rgba(0,0,0,.12); }

  /* brand lockup */
  .brand { display: flex; align-items: center; gap: 5px; }
  .brand-square { background: var(--orange); flex: none; }
  .brand-text { display: flex; flex-direction: column; line-height: 1; }
  .brand-name { font-weight: 600; color: var(--ink); letter-spacing: .02em; text-transform: uppercase; }
  .brand-by { font-weight: 500; color: var(--orange); letter-spacing: .22em; text-transform: uppercase; margin-top: 2px; }
  .brand--sm .brand-square { width: 12px; height: 12px; }
  .brand--sm .brand-name { font-size: 10px; }
  .brand--sm .brand-by { font-size: 5px; }
  .brand--lg .brand-square { width: 34px; height: 34px; }
  .brand--lg .brand-name { font-size: 24px; }
  .brand--lg .brand-by { font-size: 11px; margin-top: 5px; }
  .brand--light .brand-name { color: #e9e9e9; }

  /* footer strip */
  .footer-strip { position: absolute; left: 0; right: 0; bottom: 0; height: 15px; }
  .footer-strip .tick { position: absolute; left: 0; bottom: 0; width: 6px; height: 4px; background: var(--orange); }
  .footer-strip .bar { position: absolute; left: 6px; bottom: 0; height: 4px; background: var(--rule); }
  .footer-strip .tab {
    position: absolute; right: 0; bottom: 0; height: 15px;
    background: var(--orange); border-top-left-radius: 7px;
    color: #fff; font-size: 6.5px; letter-spacing: .14em;
    display: flex; align-items: center; justify-content: center;
  }

  /* letterhead */
  .letterhead { left: 187px; top: 63px; width: 372px; height: 527px; }
  .letterhead .brand { position: absolute; left: 33px; top: 40px; }
  .letterhead-contact { position: absolute; left: 277px; top: 27px; font-size: 4.6px; line-height: 7px; color: var(--muted); }
  .contact-row { display: flex; align-items: center; gap: 3px; }
  .contact-row svg { flex: none; }
  .letterhead .bar { width: 258px; }
  .letterhead .tab { width: 106px; }

  /* folder */
  .folder { left: 623px; top: 38px; width: 438px; height: 555px; background: var(--charcoal); }
  .folder::before { content: ""; position: absolute; left: 6px; top: 0; bottom: 0; width: 1px; background: rgba(255,255,255,.08); }
  .folder .brand { position: absolute; left: 76px; top: 254px; }

  /* business card */
  .business-card { left: 35px; top: 688px; width: 204px; height: 117px; border-radius: 4px 14px 4px 4px; overflow: hidden; }
  .business-card .brand { position: absolute; left: 10px; top: 14px; }
  .card-person { position: absolute; right: 12px; top: 58px; text-align: right; }
  .card-name { font-size: 7.5px; font-weight: 700; color: var(--orange); letter-spacing: .03em; }
  .card-role { font-size: 5px; color: var(--ink); margin-top: 2px; }
  .card-divider { position: absolute; left: 10px; right: 12px; top: 79px; height: 1px; background: #c8c8c8; }
  .card-contact { position: absolute; left: 10px; top: 83px; font-size: 5px; line-height: 8px; color: var(--ink); }
  .card-address { position: absolute; right: 12px; top: 84px; font-size: 5px; line-height: 8px; text-align: right; }
  .business-card .bar { width: 108px; }
  .business-card .tab { width: 90px; height: 12px; font-size: 5.5px; }
  .business-card .footer-strip { height: 12px; }

  /* envelope front */
  .envelope-front { left: 265px; top: 648px; width: 415px; height: 197px; }
  .envelope-front .brand { position: absolute; left: 26px; top: 16px; }
  .envelope-return { position: absolute; left: 26px; top: 38px; font-size: 4.6px; color: var(--muted); }
  .envelope-front .bar { width: 298px; }
  .envelope-front .tab { width: 107px; }

  /* envelope back */
  .envelope-back { left: 720px; top: 648px; width: 415px; height: 197px; }
  .envelope-flap { position: absolute; left: 0; right: 0; top: 0; height: 69px; background: var(--charcoal); }
  .envelope-back .brand { position: absolute; left: 141px; top: 24px; }
  .envelope-back .brand .brand-name { font-size: 11px; }
</style>
</head>
<body>

  <!-- Letterhead -->
  <section class="sheet letterhead">
    <div class="brand brand--sm">
      <span class="brand-square"></span>
      <span class="brand-text"><span class="brand-name">Linea Atelier</span><span class="brand-by">by Marc Delval</span></span>
    </div>
    <div class="letterhead-contact">
      <div>2140 Harbor Street</div>
      <div>Seaside, Oregon 97138</div>
      <div class="contact-row"><svg width="5" height="5" viewBox="0 0 10 10"><path d="M2 1l2 2-1 1.5a6 6 0 0 0 2.5 2.5L7 6l2 2-1.5 1.5C4 9 1 6 .5 2z" fill="#e8912a"/></svg>(555) 210 4471</div>
      <div class="contact-row"><svg width="5" height="5" viewBox="0 0 10 10"><rect x="2.5" y=".5" width="5" height="9" rx="1" fill="#e8912a"/></svg>(555) 384 9026</div>
      <div class="contact-row"><svg width="5" height="5" viewBox="0 0 10 10"><rect x=".5" y="2" width="9" height="6" fill="#e8912a"/></svg>adam@lineaatelier.com</div>
    </div>
    <div class="footer-strip">
      <span class="tick"></span><span class="bar"></span>
      <span class="tab">www.lineaatelier.com</span>
    </div>
  </section>

  <!-- Document folder -->
  <section class="sheet folder">
    <div class="brand brand--lg brand--light">
      <span class="brand-square"></span>
      <span class="brand-text"><span class="brand-name">Linea Atelier</span><span class="brand-by">by Marc Delval</span></span>
    </div>
  </section>

  <!-- Business card -->
  <section class="sheet business-card">
    <div class="brand brand--sm">
      <span class="brand-square"></span>
      <span class="brand-text"><span class="brand-name">Linea Atelier</span><span class="brand-by">by Marc Delval</span></span>
    </div>
    <div class="card-person">
      <div class="card-name">ADAM ROWE</div>
      <div class="card-role">CEO&amp;Founder</div>
    </div>
    <div class="card-divider"></div>
    <div class="card-contact">
      <div class="contact-row"><svg width="5" height="5" viewBox="0 0 10 10"><path d="M2 1l2 2-1 1.5a6 6 0 0 0 2.5 2.5L7 6l2 2-1.5 1.5C4 9 1 6 .5 2z" fill="#e8912a"/></svg>(555) 210 4471</div>
      <div class="contact-row"><svg width="5" height="5" viewBox="0 0 10 10"><rect x="2.5" y=".5" width="5" height="9" rx="1" fill="#e8912a"/></svg>(555) 384 9026</div>
      <div class="contact-row"><svg width="5" height="5" viewBox="0 0 10 10"><rect x=".5" y="2" width="9" height="6" fill="#e8912a"/></svg>adam@lineaatelier.com</div>
    </div>
    <div class="card-address">
      <div>2140 Harbor Street</div>
      <div>Seaside, Oregon 97138</div>
    </div>
    <div class="footer-strip">
      <span class="tick"></span><span class="bar"></span>
      <span class="tab">www.lineaatelier.com</span>
    </div>
  </section>

  <!-- Envelope, front -->
  <section class="sheet envelope-front">
    <div class="brand brand--sm">
      <span class="brand-square"></span>
      <span class="brand-text"><span class="brand-name">Linea Atelier</span><span class="brand-by">by Marc Delval</span></span>
    </div>
    <div class="envelope-return">2140 Harbor Street, Seaside, Oregon 97138</div>
    <div class="footer-strip">
      <span class="tick"></span><span class="bar"></span>
      <span class="tab">www.lineaatelier.com</span>
    </div>
  </section>

  <!-- Envelope, back -->
  <section class="sheet envelope-back">
    <div class="envelope-flap">
      <div class="brand brand--sm brand--light">
        <span class="brand-square"></span>
        <span class="brand-text"><span class="brand-name">Linea Atelier</span><span class="brand-by">by Marc Delval</span></span>
      </div>
    </div>
  </section>

</body>
</html>
```